Visit card

Industry/Entity Type

Health Care

Contact Information for Business Card

O VITALIS SYSTEMS
Odile Brevard - chef de Projet

Requirements
Must have
• 318 Gaston Lemaire Street 59710 BÉTHUNE Tel: 33 (0) 327 481 605 Mobile: 06 42 19 37 64 Web: www.quorvexsystems.example Contact: o.brevard@o-vitalissystems.example
Should not have
• Respect for color

```html
<!DOCTYPE html>
<html lang="fr">
<head>
<meta charset="utf-8">
<title>O Vitalis Systems – Carte de visite</title>
<link rel="stylesheet" href="https://fonts.googleapis.com/css2?family=Lato:wght@400;700;900&display=swap">
<style>
  :root {
    --page: #d8d3cd;
    --card: #ebe8e4;
    --charcoal: #353434;
    --red: #d3232d;
    --grey-text: #5c5a58;
    --light-text: #ece6df;
    --rim: #f4efe8;
  }
  * { box-sizing: border-box; margin: 0; padding: 0; }
  html, body {
    width: 1200px; height: 1047px; overflow: hidden;
    background: var(--page);
    font-family: "Lato", Arial, sans-serif;
  }
  .business-card {
    position: absolute; left: 60px; top: 228px;
    width: 1080px; height: 590px;
    background: var(--card);
    border-radius: 24px;
    overflow: hidden;
    box-shadow: 0 10px 30px rgba(0,0,0,0.12);
  }
  .card-art { position: absolute; inset: 0; }
  .company-name {
    position: absolute; left: 52px; top: 38px;
    color: var(--red);
    font-weight: 900;
    font-size: 46px;
    line-height: 1.05;
    letter-spacing: 1px;
    text-transform: uppercase;
  }
  .person-name {
    position: absolute; left: 52px; top: 208px;
    color: var(--red);
    font-size: 34px; font-weight: 700;
    letter-spacing: 0.5px;
    text-transform: uppercase;
  }
  .person-role {
    position: absolute; left: 52px; top: 252px;
    color: var(--grey-text);
    font-size: 24px;
  }
  .address {
    position: absolute; left: 52px; top: 300px;
    color: var(--grey-text);
    font-size: 24px; line-height: 37px;
    font-style: normal;
  }
  .contact-list {
    position: absolute; right: 44px; top: 393px;
    list-style: none;
    color: var(--light-text);
    font-size: 22px;
  }
  .contact-list li {
    display: flex; justify-content: flex-end; align-items: center;
    height: 35.5px; gap: 12px;
  }
  .contact-icon { width: 16px; height: 16px; flex: none; }
</style>
</head>
<body>
  <div class="business-card">
    <svg class="card-art" viewBox="0 0 1080 590" width="1080" height="590" aria-hidden="true">
      <path d="M0,462 C160,440 300,410 430,352 C600,276 820,200 1080,150 L1080,590 L0,590 Z" fill="var(--charcoal)"/>
      <path d="M0,382 C90,430 220,438 340,392 C520,322 740,226 1080,150" fill="none" stroke="var(--red)" stroke-width="12"/>
      <path d="M0,420 C120,452 260,446 380,392 C560,312 780,220 1080,170" fill="none" stroke="var(--red)" stroke-width="6"/>
      <path d="M0,440 C140,466 290,452 410,388" fill="none" stroke="var(--rim)" stroke-width="3"/>
      <circle cx="880" cy="178" r="150" fill="var(--rim)"/>
      <circle cx="880" cy="178" r="128" fill="none" stroke="var(--charcoal)" stroke-width="34"/>
    </svg>

    <div class="company-name">O Vitalis<br>Systems</div>

    <div class="person-name">Odile Brevard</div>
    <div class="person-role">Chef de Projet</div>
    <address class="address">318 Rue Gaston Lemaire<br>59710 BÉTHUNE</address>

    <ul class="contact-list">
      <li>+33 (0) 327 481 605
        <svg class="contact-icon" viewBox="0 0 16 16"><path d="M3 1.5l3 3-1.6 1.8c.8 2 2.3 3.5 4.3 4.3L10.5 9l3 3-1.8 2.5C6.5 14 2 9.5 1.5 4.3z" fill="none" stroke="var(--red)" stroke-width="1.4"/></svg>
      </li>
      <li>06 42 19 37 64
        <svg class="contact-icon" viewBox="0 0 16 16"><rect x="4" y="1" width="8" height="14" rx="1.5" fill="none" stroke="var(--red)" stroke-width="1.5"/><circle cx="8" cy="12.3" r="1" fill="var(--red)"/></svg>
      </li>
      <li>www.quorvexsystems.example
        <svg class="contact-icon" viewBox="0 0 16 16"><circle cx="8" cy="8" r="6.5" fill="none" stroke="var(--red)" stroke-width="1.4"/><ellipse cx="8" cy="8" rx="2.8" ry="6.5" fill="none" stroke="var(--red)" stroke-width="1.2"/><path d="M1.5 8h13" stroke="var(--red)" stroke-width="1.2"/></svg>
      </li>
      <li>o.brevard@o-vitalissystems.example
        <svg class="contact-icon" viewBox="0 0 16 16"><rect x="1.5" y="3.5" width="13" height="9" fill="none" stroke="var(--red)" stroke-width="1.4"/><path d="M1.5 3.5L8 9l6.5-5.5" fill="none" stroke="var(--red)" stroke-width="1.4"/></svg>
      </li>
    </ul>
  </div>
</body>
</html>
```